Valdane Companies Business Card Design

We need a new business card for our Private Equity Real Estate Development firm, “Valdane” and our EB-5 regional center “Thornmere Regional Center” on one card. We prefer a design that is simple, elegant, and represents the luxury products we design and build as well as the financial security and stability our successful history has produced. We are an industry leader in our field and 3rd generation family business that has evolved into an institutional quality investment platform. Considered design size is standard business card dimensions (3.5 x 2 inches with an additional 1/8 inch space for design elements or backgrounds that extend beyond the finished size of your piece.

Target Market(s)

• High net worth individuals
• Highly skilled technical workers and physicians in the US seeking investment-based immigration opportunities
• Sophisticated private equity investors
• Intermediary partners include domestic attorneys and investment brokers, as well as international agent networks
• US real estate developers

Industry/Entity Type

Finance

Contact Information for Business Card

(Providing placeholder info for personal information, please design for longer character spaces, longer names and addresses etc..)
• Logo for Valdane
• Logo for Thornmere Regional Center
• Full name: Marcus Valdane
• Job title: CEO
• Email address: mvaldane@valdanecompanies.com
• Cell phone number: +1.555.314.2287
• Office number +1.555.628.4410
• Office address: Larkfield Court 5, 4817 Vista Orilla, Brierwood, CA.
• Website: www.valdanecompanies.com

Font styles to use
Serif
Sans Serif

Colors
ec1f27
ffffff
000000

Requirements
Must have
• • Logo for Valdane
• • Logo for Thornmere Regional Center
• - Use rounded corners
• (See .ai file included for logos)
Nice to have
• • Simple, elegant design
• • Aesthetically compatible with our website design (www.valdanecompanies.com)
• • Color palette including but not limited to white, black, and red (as per logos)
Should not have
• - Not too much red color
• - Do not stack both logos on top of each other

```html
<!DOCTYPE html>
<html lang="en">
<head>
<meta charset="UTF-8">
<title>Valdane Companies – Business Card</title>
<link href="https://fonts.googleapis.com/css2?family=Libre+Baskerville:wght@400;700&display=swap" rel="stylesheet">
<style>
  :root {
    --backdrop: #26272b;
    --slate: #435366;
    --crimson: #a51f35;
    --paper: #ffffff;
    --ink: #2b2f36;
    --silver: #d9dde2;
    --rule: #3d4a5c;
  }
  * { box-sizing: border-box; margin: 0; padding: 0; }
  html, body {
    width: 1200px; height: 800px; overflow: hidden;
    background: var(--backdrop);
    font-family: "Libre Baskerville", "Times New Roman", serif;
  }
  .canvas { position: relative; width: 1200px; height: 800px; }

  .card {
    position: absolute;
    width: 540px; height: 309px;
    border-radius: 14px;
    overflow: hidden;
  }

  /* Back side */
  .card-back { left: 70px; top: 70px; background: var(--slate); color: var(--silver); }
  .card-back .brand {
    position: absolute; left: 0; right: 0; top: 108px;
    display: flex; justify-content: center; align-items: center; gap: 14px;
  }
  .brand-square { width: 26px; height: 26px; background: currentColor; flex: none; }
  .brand-name {
    font-weight: 700; font-size: 24px; letter-spacing: 2px; line-height: 1.15;
    text-transform: uppercase;
  }
  .card-back .website {
    position: absolute; left: 0; right: 0; bottom: 62px;
    text-align: center; font-size: 11px; letter-spacing: 3px; color: var(--paper);
  }

  /* Front side */
  .card-front { left: 590px; top: 420px; background: var(--paper); color: var(--ink); }
  .card-front .brand {
    position: absolute; right: 40px; top: 44px;
    display: flex; align-items: center; gap: 12px;
    color: var(--crimson);
  }
  .card-front .brand-name { font-size: 21px; }

  .holder { position: absolute; left: 28px; top: 140px; }
  .holder-name { font-size: 19px; font-weight: 700; color: var(--crimson); line-height: 1.3; }
  .holder-title { font-size: 12px; color: var(--ink); line-height: 1.3; margin-top: 1px; }
  .divider {
    position: absolute; left: 28px; right: 28px; top: 192px;
    height: 1px; background: var(--rule);
  }

  .contact-band {
    position: absolute; left: 0; right: 0; top: 206px; height: 82px;
    background: var(--crimson); color: var(--paper);
    display: flex; justify-content: space-between; align-items: center;
    padding: 0 28px; font-size: 11px; line-height: 1.7;
  }
  .contact-list { list-style: none; }
  .contact-list li { display: flex; align-items: center; gap: 8px; }
  .contact-list svg { width: 13px; height: 13px; flex: none; }
  .address { text-align: right; font-style: normal; }
  .accent-strip {
    position: absolute; left: 0; right: 0; top: 288px; bottom: 0;
    background: var(--slate);
  }
</style>
</head>
<body>
<main class="canvas">

  <section class="card card-back" aria-label="Card back">
    <div class="brand">
      <span class="brand-square"></span>
      <span class="brand-name">Thornmere<br>Regional Center</span>
    </div>
    <p class="website">www.valdanecompanies.com</p>
  </section>

  <section class="card card-front" aria-label="Card front">
    <div class="brand">
      <span class="brand-square"></span>
      <span class="brand-name">Thornmere<br>Regional Center</span>
    </div>

    <div class="holder">
      <p class="holder-name">Marcus Valdane</p>
      <p class="holder-title">CEO</p>
    </div>
    <div class="divider"></div>

    <div class="contact-band">
      <ul class="contact-list">
        <li>
          <svg viewBox="0 0 14 14" fill="none" stroke="currentColor" stroke-width="1.2"><circle cx="7" cy="7" r="6.2"/><rect x="5" y="3.5" width="4" height="7" rx="0.6"/></svg>
          +1.555.314.2287
        </li>
        <li>
          <svg viewBox="0 0 14 14" fill="none" stroke="currentColor" stroke-width="1.2"><circle cx="7" cy="7" r="6.2"/><path d="M4 5.5q3-2 6 0l-0.8 1.2h-4.4z M4.8 8h4.4v2h-4.4z"/></svg>
          +1.555.628.4410
        </li>
        <li>
          <svg viewBox="0 0 14 14" fill="none" stroke="currentColor" stroke-width="1.2"><circle cx="7" cy="7" r="6.2"/><rect x="3.8" y="4.8" width="6.4" height="4.4"/><path d="M3.8 4.8l3.2 2.4 3.2-2.4"/></svg>
          mvaldane@valdanecompanies.com
        </li>
      </ul>
      <address class="address">
        Larkfield Court 5<br>
        4817 Vista Orilla<br>
        Brierwood, CA.
      </address>
    </div>
    <div class="accent-strip"></div>
  </section>

</main>
</body>
</html>
```